Full Page Tolver 250 Ad

We need a full page magazine ad. Our company is a site construction company - meaning we build lakes, ponds, do brush clearing for farmers and ranchers. For commercial customers, we build building pads, site clearing, pavement and soil stabilization. The final design should show what we do. Our website is www.pendrowgrading.com

```html
<!DOCTYPE html>
<html lang="en">
<head>
<meta charset="utf-8">
<title>Tolver 250 – Full Page Ad</title>
<link rel="stylesheet" href="https://fonts.googleapis.com/css2?family=Bebas+Neue&family=Poppins:wght@400;500;600&display=swap">
<style>
  :root {
    --ink: #111111;
    --charcoal: #2b2b2b;
    --gold: #f2b531;
    --paper: #ffffff;
    --mist: #e6e6e8;
    --page-bg: #8a8a8a;
  }
  * { margin: 0; padding: 0; box-sizing: border-box; }
  html, body { width: 727px; height: 1200px; overflow: hidden; background: var(--page-bg); }
  .ad {
    position: relative;
    width: 727px;
    height: 1200px;
    overflow: hidden;
    background: var(--paper);
    font-family: "Poppins", Arial, sans-serif;
  }
  .ad-art { position: absolute; inset: 0; width: 727px; height: 1200px; }

  .brand {
    position: absolute;
    left: 38px;
    top: 92px;
    display: flex;
    align-items: center;
    gap: 12px;
  }
  .brand-mark { width: 26px; height: 26px; background: var(--gold); }
  .brand-name {
    font-family: "Bebas Neue", Impact, sans-serif;
    font-size: 66px;
    line-height: 1;
    color: var(--ink);
    letter-spacing: 1px;
  }

  .headline {
    position: absolute;
    left: 57px;
    top: 300px;
    font-family: "Bebas Neue", Impact, sans-serif;
    color: var(--paper);
    line-height: 0.92;
    transform: scaleY(1.12);
    transform-origin: top left;
  }
  .headline span { display: block; }
  .headline .lead { font-size: 56px; }
  .headline .years { font-size: 92px; color: var(--gold); }
  .headline .tail { font-size: 60px; }

  .tagline {
    position: absolute;
    left: 40px;
    width: 648px;
    top: 612px;
    text-align: center;
    color: var(--paper);
    font-size: 17px;
    line-height: 1.2;
  }

  .rural-services {
    position: absolute;
    left: 40px;
    width: 312px;
    top: 762px;
    text-align: center;
    font-size: 23px;
    font-weight: 500;
    line-height: 1.12;
    color: var(--ink);
  }

  .commercial-tag {
    position: absolute;
    left: 384px;
    top: 766px;
    width: 290px;
    height: 38px;
    background: var(--ink);
    transform: skewX(-10deg);
    display: flex;
    align-items: center;
    justify-content: center;
  }
  .commercial-tag p {
    transform: skewX(10deg);
    color: var(--paper);
    font-size: 16px;
    font-weight: 600;
  }
  .commercial-tag .accent { color: var(--gold); }
  .commercial-services {
    position: absolute;
    left: 370px;
    width: 320px;
    top: 812px;
    text-align: center;
    font-size: 15px;
    line-height: 1.2;
    color: var(--ink);
  }

  .contact {
    position: absolute;
    left: 0;
    right: 0;
    top: 1102px;
    display: flex;
    justify-content: center;
    align-items: center;
    gap: 44px;
    font-family: "Bebas Neue", Impact, sans-serif;
    font-size: 50px;
    color: var(--ink);
    line-height: 1;
  }
  .contact-item { display: flex; align-items: center; gap: 12px; }
  .contact-item.web { font-size: 46px; }
  .contact-icon { width: 38px; height: 38px; flex: none; }
</style>
</head>
<body>
<main class="ad">
  <svg class="ad-art" viewBox="0 0 727 1200" aria-hidden="false">
    <defs>
      <linearGradient id="heroPhotoTone" x1="0" y1="0" x2="0.4" y2="1">
        <stop offset="0" stop-color="#4f80bd"/>
        <stop offset="0.25" stop-color="#c59a2a"/>
        <stop offset="0.55" stop-color="#6b6456"/>
        <stop offset="1" stop-color="#d9ccae"/>
      </linearGradient>
      <linearGradient id="detailPhotoTone" x1="0" y1="0" x2="1" y2="1">
        <stop offset="0" stop-color="#d8c9a4"/>
        <stop offset="0.5" stop-color="#c9a040"/>
        <stop offset="1" stop-color="#3e3a34"/>
      </linearGradient>
      <linearGradient id="pondPhotoTone" x1="0" y1="0" x2="0" y2="1">
        <stop offset="0" stop-color="#7fa6cf"/>
        <stop offset="0.45" stop-color="#6f7550"/>
        <stop offset="1" stop-color="#6a5a44"/>
      </linearGradient>
      <linearGradient id="padPhotoTone" x1="0" y1="0" x2="0" y2="1">
        <stop offset="0" stop-color="#8c9a6e"/>
        <stop offset="0.35" stop-color="#e5dfd6"/>
        <stop offset="1" stop-color="#c9bfae"/>
      </linearGradient>
      <linearGradient id="shorePhotoTone" x1="0" y1="0" x2="0" y2="1">
        <stop offset="0" stop-color="#8fb2d6"/>
        <stop offset="0.4" stop-color="#4e8a86"/>
        <stop offset="0.65" stop-color="#8a7a62"/>
        <stop offset="1" stop-color="#5a4a3a"/>
      </linearGradient>
      <linearGradient id="bandFade" x1="0" y1="0" x2="1" y2="0">
        <stop offset="0" stop-color="#262626"/>
        <stop offset="1" stop-color="#333333"/>
      </linearGradient>
      <filter id="cardShadow" x="-10%" y="-10%" width="120%" height="130%">
        <feDropShadow dx="0" dy="3" stdDeviation="3" flood-opacity="0.3"/>
      </filter>
    </defs>

    <!-- dark headline band -->
    <polygon class="headline-band" points="0,228 727,228 727,748 0,664" fill="url(#bandFade)"/>

    <!-- commercial panel -->
    <polygon class="commercial-panel" points="385,692 727,746 727,1070 338,1070" fill="var(--mist)"/>

    <!-- gold accent stripe -->
    <polygon class="accent-stripe" points="0,668 162,699 0,724" fill="var(--gold)"/>

    <!-- gold footer band -->
    <polygon class="footer-band" points="0,950 727,1062 727,1200 0,1200" fill="var(--gold)"/>

    <!-- hero photo frame -->
    <path class="hero-frame" d="M432,-10 L292,296 Q278,329 302,352 L540,578 Q562,596 582,574 L740,402 L740,-10 Z"
          fill="var(--gold)"/>
    <path role="img" aria-label="Photo: large yellow earthmoving scraper on a sandy site under blue sky"
          d="M444,-10 L303,298 Q292,327 312,346 L543,565 Q561,580 576,562 L740,388 L740,-10 Z"
          fill="url(#heroPhotoTone)"/>

    <!-- detail photo diamond -->
    <path class="detail-frame" d="M478,252 Q490,252 500,266 L606,404 Q618,422 606,440 L500,584 Q478,606 456,584 L350,440 Q338,422 350,404 L456,266 Q466,252 478,252 Z"
          fill="var(--ink)"/>
    <path d="M478,262 Q488,262 496,274 L598,406 Q608,422 598,438 L496,576 Q478,594 460,576 L358,438 Q348,422 358,406 L460,274 Q468,262 478,262 Z"
          fill="var(--paper)"/>
    <path role="img" aria-label="Photo: close-up of a yellow soil stabilizer attachment on a tractor"
          d="M478,268 Q487,268 494,279 L593,408 Q601,422 593,436 L494,571 Q478,587 462,571 L363,436 Q355,422 363,408 L462,279 Q469,268 478,268 Z"
          fill="url(#detailPhotoTone)"/>

    <!-- project photo row -->
    <g class="project-photos" filter="url(#cardShadow)">
      <rect x="28" y="890" width="222" height="182" rx="16" fill="var(--paper)"/>
      <rect x="246" y="890" width="223" height="182" rx="16" fill="var(--paper)"/>
      <rect x="465" y="890" width="223" height="182" rx="16" fill="var(--paper)"/>
    </g>
    <rect role="img" aria-label="Photo: freshly shaped pond earthwork with trees on the horizon"
          x="33" y="895" width="212" height="172" rx="12" fill="url(#pondPhotoTone)"/>
    <rect role="img" aria-label="Photo: aerial view of a commercial building pad and parking lot"
          x="251" y="895" width="213" height="172" rx="12" fill="url(#padPhotoTone)"/>
    <rect role="img" aria-label="Photo: red tractor pulling a scraper along a lake shoreline"
          x="470" y="895" width="213" height="172" rx="12" fill="url(#shorePhotoTone)"/>
  </svg>

  <div class="brand">
    <span class="brand-mark"></span>
    <span class="brand-name">Tolver 250</span>
  </div>

  <h1 class="headline">
    <span class="lead">With over</span>
    <span class="years">50 Years</span>
    <span class="tail">of experience</span>
    <span class="tail">in the industry,</span>
  </h1>

  <p class="tagline">We have what it takes to help you develop your land for<br>your long or short term goals.</p>

  <p class="rural-services">We build lakes • ponds •<br>do brush clearing for<br>farmers and ranchers.</p>

  <div class="commercial-tag"><p>For commercial <span class="accent">customers,</span></p></div>
  <p class="commercial-services">we build building pads • site clearing,<br>pavement and soil stabilization.</p>

  <div class="contact">
    <div class="contact-item phone">
      <svg class="contact-icon" viewBox="0 0 40 40" aria-hidden="true">
        <circle cx="20" cy="20" r="19" fill="var(--ink)"/>
        <path d="M14 10c1-.6 2-.4 2.6.6l2 3.4c.5.9.3 1.9-.5 2.5l-1.4 1c.9 2.4 2.9 4.4 5.3 5.4l1-1.4c.6-.8 1.6-1 2.5-.5l3.4 2c1 .6 1.2 1.6.6 2.6l-1.2 1.8c-.8 1.2-2.3 1.7-3.7 1.2C18.3 27 13 21.7 11.4 15.4c-.4-1.4.1-2.9 1.3-3.7z" fill="var(--gold)"/>
      </svg>
      <span>361.555-0148</span>
    </div>
    <div class="contact-item web">
      <svg class="contact-icon" viewBox="0 0 40 40" aria-hidden="true">
        <circle cx="20" cy="20" r="19" fill="var(--ink)"/>
        <g fill="none" stroke="var(--gold)" stroke-width="1.8">
          <circle cx="20" cy="20" r="10"/>
          <ellipse cx="20" cy="20" rx="4.5" ry="10"/>
          <line x1="10" y1="20" x2="30" y2="20"/>
          <line x1="12" y1="14.5" x2="28" y2="14.5"/>
          <line x1="12" y1="25.5" x2="28" y2="25.5"/>
        </g>
      </svg>
      <span>PENDROWGRADING.COM</span>
    </div>
  </div>
</main>
</body>
</html>
```